Bring me business with this creative business card

Design my new business card. I am looking for something different with an impact. People will take a look at this card & they will 1- see how different & creative I am, 2-understand what I do 3- Call me to meet me!

I make videos with a message, testimonials. I am dynamic, fun, creative & human. My new website is in construction but in the meantime you can check this old one: brightpath.ca & another one Tidebloom.com & tidebloom facebook page.
I make videos. sometimes with a cameraman, sometimes with my phone. As an ex Public Relations agent, the message is the most important thing for me. I want to make my clients shine! When they start with me they often remind me of a lamb, when I finish coaching them they are powerful like LIONS! That's why I need a powerful business card!

Target Market(s)

Entrepreneurs, solo entrepreneurs, small & medium companies & start ups. People i will meet while networking. People that need videos on their website & social Networks to get attention, to be visible. men & women. From 35 to 49 years old.
I am an ex Public relations agent. I used to send clients in traditional medias, now with videos they have more chances to be seen on google the new media. I do videos of the president, his team, his loyal clients saying how great the company is & expert videos like series so people can be seen for example every 1 st of every month with a short 2 minute video. Also with my 20 years in marketing & communications I can coach & give tips to anybody who needs it.
Target: anybody who would like my old website brightpath.ca & I also have another website but it will be off line soon: tidebloom.com could give you ideas.

Industry/Entity Type

Communications

Contact Information for Business Card

I am in Montreal,So the business cards have to be the usual size like we have in Montreal: 9 cm x 5 cm
Details:My text: Mathilde Tessier Communication coach/Chief Lion. "Creating Videos as unique as you" off: 514-555-0147 cell: 514-555-0183. tidebloom.com
mathilde@tidebloom.com logo facebook, youtube, instagram

Colors
f37122

Requirements
Must have
• Dynamic, happy. Orange. Be creative in the look but NOT the shape of the card. Easy to read. Big enough to read.
Should not have
• No funny shapes: no round, no square, just the usual. I love creative but NOT on shape.

```html
<!DOCTYPE html>
<html lang="en">
<head>
<meta charset="utf-8">
<title>Tidebloom – Business Card</title>
<link rel="stylesheet" href="https://fonts.googleapis.com/css2?family=Cinzel:wght@700&family=Open+Sans:wght@400;600&family=Tinos&display=swap">
<style>
  :root {
    --orange: #f37122;
    --gold: #f5a623;
    --ink: #2a2a2a;
    --card-white: #ffffff;
    --card-black: #0d0d0d;
    --backdrop: #ecebe8;
  }
  * { box-sizing: border-box; margin: 0; padding: 0; }
  html, body {
    width: 1200px; height: 900px; overflow: hidden;
    background: var(--backdrop);
  }
  .sheet {
    width: 1200px; height: 900px;
    display: flex; flex-direction: column;
    align-items: center; justify-content: center; gap: 50px;
  }
  .card {
    width: 630px; height: 350px;
    position: relative;
    box-shadow: 0 6px 18px rgba(0,0,0,.18);
  }
  /* back side */
  .card--back {
    background: var(--card-black);
    display: flex; flex-direction: column;
    align-items: center; justify-content: center; gap: 16px;
  }
  .back-dot {
    width: 110px; height: 110px; border-radius: 50%;
    background: var(--orange);
  }
  .back-name {
    font-family: "Open Sans", sans-serif; font-weight: 600;
    font-size: 26px; color: var(--orange);
  }
  /* front side */
  .card--front { background: var(--card-white); }
  .brand {
    position: absolute; left: 60px; top: 80px; width: 200px;
    display: flex; flex-direction: column; align-items: center; gap: 14px;
  }
  .brand-dot {
    width: 100px; height: 100px; border-radius: 50%;
    background: var(--orange);
  }
  .brand-name {
    font-family: "Open Sans", sans-serif; font-weight: 600;
    font-size: 22px; color: var(--orange); line-height: 1;
  }
  .divider {
    position: absolute; left: 285px; top: 62px;
    width: 1px; height: 170px; background: var(--orange);
  }
  .contact {
    position: absolute; left: 305px; top: 62px;
  }
  .person-name {
    font-family: "Cinzel", serif; font-weight: 700;
    font-size: 23px; letter-spacing: 1px; color: var(--gold);
    line-height: 1.1;
  }
  .person-role {
    font-family: "Open Sans", sans-serif; font-size: 13px;
    color: var(--ink); margin-bottom: 16px;
  }
  .contact-list { list-style: none; }
  .contact-list li {
    display: flex; align-items: center; gap: 9px;
    font-family: "Open Sans", sans-serif; font-size: 13.5px;
    color: var(--ink); line-height: 22px;
  }
  .contact-list svg { width: 11px; height: 11px; fill: var(--orange); flex: none; }
  .tagline {
    position: absolute; left: 0; right: 0; bottom: 42px;
    text-align: center;
    font-family: "Tinos", serif; font-size: 21px;
    letter-spacing: 0.5px; color: var(--orange);
    text-transform: uppercase;
  }
</style>
</head>
<body>
<main class="sheet">
  <section class="card card--back" aria-label="Card back">
    <div class="back-dot"></div>
    <div class="back-name">Tidebloom</div>
  </section>

  <section class="card card--front" aria-label="Card front">
    <div class="brand">
      <div class="brand-dot"></div>
      <div class="brand-name">Tidebloom</div>
    </div>
    <div class="divider"></div>
    <div class="contact">
      <div class="person-name">MATHILDE T</div>
      <div class="person-role">Communication Coach/Chief Lion</div>
      <ul class="contact-list">
        <li><svg viewBox="0 0 12 12"><path d="M1 4c0-2 2-3 5-3s5 1 5 3v1H8V4H4v1H1zM2 6h8l1 5H1z"/></svg>514-555-0147</li>
        <li><svg viewBox="0 0 12 12"><path d="M3 0h6a1 1 0 0 1 1 1v10a1 1 0 0 1-1 1H3a1 1 0 0 1-1-1V1a1 1 0 0 1 1-1zm0 2v7h6V2z"/></svg>514-555-0183</li>
        <li><svg viewBox="0 0 12 12"><path d="M0 2h12v1L6 7 0 3zm0 2.5 6 4 6-4V10H0z"/></svg>mathilde@tidebloom.com</li>
        <li><svg viewBox="0 0 12 12"><circle cx="6" cy="6" r="6"/></svg>www.tidebloom.com</li>
      </ul>
    </div>
    <div class="tagline">Creating videos as unique as you</div>
  </section>
</main>
</body>
</html>
```